New National Dermatology Group needs a business card!

We need a business card for our new national company that has 3 brands within the business:
Lumora Clinics Australia, Tessaly Clinics Australia and Corvane Clinics Australia.
We help people access dermatology services close to home throughout Australia.
We need a business card that has:
all 3 logos on it,
Our websites (there are three, listed above)
Our email (there are three, listed above)
The location of our first clinic: 41 Willow Rd Parramatta (this can then be changed for each location as required)

```html
<!DOCTYPE html>
<html lang="en">
<head>
<meta charset="utf-8">
<title>Business Card – Corvane, Lumora and Tessaly Clinics Australia</title>
<link rel="stylesheet" href="https://fonts.googleapis.com/css2?family=Open+Sans:wght@400;600&display=swap">
<style>
  :root {
    --backdrop: #b8b8b8;
    --card-white: #ffffff;
    --card-orange: #f4862b;
    --brand-brown: #7a3a14;
    --brand-green: #1aaa4a;
    --brand-orange: #f0832a;
    --ink: #1c1c1c;
    --shadow: #222222;
  }
  html, body {
    margin: 0;
    padding: 0;
    width: 1200px;
    height: 801px;
    overflow: hidden;
    background: var(--backdrop);
    font-family: "Open Sans", sans-serif;
  }
  .stage { position: relative; width: 1200px; height: 801px; }
  .card {
    position: absolute;
    top: 274px;
    width: 443px;
    height: 263px;
    box-shadow: 2px 2px 1px var(--shadow);
  }
  .card--front { left: 153px; background: var(--card-white); }
  .card--back { left: 625px; background: var(--card-orange); }

  .brand-row { position: absolute; left: 45px; width: 360px; height: 50px; }
  .brand-row--corvane { top: 29px; --accent: var(--brand-brown); }
  .brand-row--lumora { top: 109px; --accent: var(--brand-green); }
  .brand-row--tessaly { top: 190px; --accent: var(--brand-orange); }

  .brand-name {
    position: absolute;
    left: 0;
    top: 0;
    width: 182px;
    color: var(--accent);
    font-weight: 600;
    text-align: center;
  }
  .brand-name__main { display: block; font-size: 33px; line-height: 33px; letter-spacing: 2px; text-transform: uppercase; }
  .brand-name__sub { display: block; font-size: 9px; line-height: 12px; letter-spacing: 5.6px; text-transform: uppercase; }

  .divider {
    position: absolute;
    left: 198px;
    top: 1px;
    width: 1px;
    height: 45px;
    background: var(--accent);
  }
  .contact {
    position: absolute;
    left: 221px;
    top: -3px;
    margin: 0;
    padding: 0;
    list-style: none;
    font-size: 12.5px;
    color: var(--ink);
  }
  .contact li { display: flex; align-items: center; height: 15px; white-space: nowrap; }
  .contact .contact__address { margin-top: 6px; }
  .contact svg { width: 12px; height: 11px; margin-right: 8px; flex: none; }
  .icon-fill { fill: var(--accent); }
  .icon-line { fill: none; stroke: var(--accent); stroke-width: 1.2; }

  .back-brand {
    position: absolute;
    left: 0;
    right: 0;
    top: 102px;
    color: var(--ink);
    font-weight: 600;
    text-align: center;
  }
  .back-brand .brand-name__main { font-size: 38px; line-height: 40px; letter-spacing: 3.4px; }
  .back-brand .brand-name__sub { font-size: 10.5px; letter-spacing: 6.4px; }
</style>
</head>
<body>
<main class="stage">
  <section class="card card--front" aria-label="Card front">
    <div class="brand-row brand-row--corvane">
      <div class="brand-name"><span class="brand-name__main">Corvane</span><span class="brand-name__sub">Clinics Australia</span></div>
      <div class="divider"></div>
      <ul class="contact">
        <li><svg viewBox="0 0 12 11"><rect class="icon-fill" x="0" y="1" width="12" height="9"/><path d="M0 1 L6 6 L12 1" stroke="#fff" fill="none" stroke-width="1"/></svg>info@corvane.co.uk</li>
        <li><svg viewBox="0 0 12 12"><circle class="icon-line" cx="6" cy="6" r="5"/><ellipse class="icon-line" cx="6" cy="6" rx="2.2" ry="5"/><path class="icon-line" d="M1 6 H11 M2 3.5 H10 M2 8.5 H10"/></svg>www.corvane.co.uk</li>
        <li class="contact__address">41 Willow Rd Parramatta</li>
      </ul>
    </div>
    <div class="brand-row brand-row--lumora">
      <div class="brand-name"><span class="brand-name__main">Lumora</span><span class="brand-name__sub">Clinics Australia</span></div>
      <div class="divider"></div>
      <ul class="contact">
        <li><svg viewBox="0 0 12 11"><rect class="icon-fill" x="0" y="1" width="12" height="9"/><path d="M0 1 L6 6 L12 1" stroke="#fff" fill="none" stroke-width="1"/></svg>info@lumora.co.uk</li>
        <li><svg viewBox="0 0 12 12"><circle class="icon-line" cx="6" cy="6" r="5"/><ellipse class="icon-line" cx="6" cy="6" rx="2.2" ry="5"/><path class="icon-line" d="M1 6 H11 M2 3.5 H10 M2 8.5 H10"/></svg>www.lumora.co.uk</li>
        <li class="contact__address">41 Willow Rd Parramatta</li>
      </ul>
    </div>
    <div class="brand-row brand-row--tessaly">
      <div class="brand-name"><span class="brand-name__main">Tessaly</span><span class="brand-name__sub">Clinics Australia</span></div>
      <div class="divider"></div>
      <ul class="contact">
        <li><svg viewBox="0 0 12 11"><rect class="icon-fill" x="0" y="1" width="12" height="9"/><path d="M0 1 L6 6 L12 1" stroke="#fff" fill="none" stroke-width="1"/></svg>info@tessaly.co.uk</li>
        <li><svg viewBox="0 0 12 12"><circle class="icon-line" cx="6" cy="6" r="5"/><ellipse class="icon-line" cx="6" cy="6" rx="2.2" ry="5"/><path class="icon-line" d="M1 6 H11 M2 3.5 H10 M2 8.5 H10"/></svg>www.tessaly.co.uk</li>
        <li class="contact__address">41 Willow Rd Parramatta</li>
      </ul>
    </div>
  </section>

  <section class="card card--back" aria-label="Card back">
    <div class="back-brand"><span class="brand-name__main">Corvane</span><span class="brand-name__sub">Clinics Australia</span></div>
  </section>
</main>
</body>
</html>
```